New business card/stationary for a consulting company

I am looking for a clean and very professional looking business card for my consulting company as well as corresponding stationary. I am uploading our logo. I like simple and powerful for the feel. No graphics but I am open on everything else. Below is my contact information but would like the final to be in a version I can add my employees information into and print. Thank you.

Daniel Whitcombe
dan@ferncliffadvisory.com
2870 North 9th Avenue, Summit Floor, Elm Ridge, Illinois 60531
www.ferncliffadvisory.com

Industry/Entity Type

Consulting

Contact Information for Business Card

Daniel Whitcombe
dan@ferncliffadvisory.com
www.ferncliffadvisory.com

Font styles to use
Serif
Sans Serif

Requirements
Must have
• Our logo and the business card details.
Nice to have
• our website www.ferncliffadvisory.com

```html
<!DOCTYPE html>
<html lang="en">
<head>
<meta charset="utf-8">
<title>Ferncliff Advisory — Business Card</title>
<link rel="stylesheet" href="https://fonts.googleapis.com/css2?family=Marcellus&family=Roboto:wght@400&display=swap">
<style>
  :root {
    --backdrop: #e6e6e6;
    --navy: #112b5b;
    --navy-text: #1a2d5e;
    --paper: #f7f7f7;
    --ink: #2a2a2a;
    --white: #ffffff;
  }
  * { margin: 0; padding: 0; box-sizing: border-box; }
  html, body {
    width: 1200px;
    height: 576px;
    overflow: hidden;
    background: var(--backdrop);
  }
  .canvas {
    position: relative;
    width: 1200px;
    height: 576px;
  }
  .card {
    position: absolute;
    top: 139px;
    width: 484px;
    height: 292px;
    border-radius: 14px;
  }
  .card-front {
    left: 82px;
    background: var(--navy);
  }
  .card-back {
    left: 602px;
    background: var(--paper);
  }
  .brand-front {
    position: absolute;
    left: 0;
    right: 0;
    top: 164px;
    display: flex;
    align-items: center;
    justify-content: center;
    gap: 12px;
    font-family: "Marcellus", serif;
    font-size: 26px;
    letter-spacing: 1.5px;
    color: var(--white);
  }
  .brand-mark {
    width: 14px;
    height: 14px;
    background: var(--white);
  }
  .holder-name {
    position: absolute;
    left: 22px;
    top: 44px;
    font-family: "Marcellus", serif;
    font-size: 20px;
    letter-spacing: 1.2px;
    color: var(--navy-text);
  }
  .contact {
    position: absolute;
    left: 22px;
    top: 190px;
    font-family: "Roboto", sans-serif;
    font-size: 12.5px;
    line-height: 20px;
    color: var(--ink);
  }
  .contact-line {
    display: flex;
    align-items: center;
    gap: 9px;
  }
  .contact-line svg { width: 11px; height: 11px; }
  .address { margin-top: 2px; line-height: 19.5px; }
  .brand-back {
    position: absolute;
    right: 28px;
    bottom: 30px;
    font-family: "Marcellus", serif;
    font-size: 15px;
    letter-spacing: 1px;
    color: var(--navy-text);
  }
</style>
</head>
<body>
<main class="canvas">
  <section class="card card-front" aria-label="Card front">
    <div class="brand-front">
      <span class="brand-mark"></span>
      <span class="brand-name">FERNCLIFF ADVISORY</span>
    </div>
  </section>

  <section class="card card-back" aria-label="Card back">
    <h1 class="holder-name">DANIEL WHITCOMBE</h1>
    <div class="contact">
      <div class="contact-line">
        <svg viewBox="0 0 12 12" aria-hidden="true">
          <rect x="0.5" y="2" width="11" height="8" fill="#1a2d5e"/>
          <path d="M0.8 2.4 L6 6.6 L11.2 2.4" fill="none" stroke="#ffffff" stroke-width="1"/>
        </svg>
        <span>dan@ferncliffadvisory.com</span>
      </div>
      <div class="contact-line">
        <svg viewBox="0 0 12 12" aria-hidden="true">
          <circle cx="6" cy="6" r="5" fill="#1a2d5e"/>
          <path d="M1 6 H11 M6 1 C3.5 3.5 3.5 8.5 6 11 M6 1 C8.5 3.5 8.5 8.5 6 11" fill="none" stroke="#ffffff" stroke-width="0.7"/>
        </svg>
        <span>www.ferncliffadvisory.com</span>
      </div>
      <p class="address">2870 North 9th Avenue, Summit<br>Floor, Elm Ridge, Illinois 60531</p>
    </div>
    <div class="brand-back">FERNCLIFF ADVISORY</div>
  </section>
</main>
</body>
</html>
```